Business Card Design - Photographer

I am a landscape photographer and I require a business card design. 

I require two designs:
1)  a double sided business card
 and
b)  a single sided business card 

The single sided design can either be the same as the double sided (with just one side having all the information)....or it can be an entire new design. Its up to you.

My corporate colours are (CMYK):

Blue   69, 32, 0, 0
Grey  72,  64,  47,  31
Green  32,  2,  91,  0
Yellow   0, 19, 92, 0
Orange  0, 39, 75, 0

Colour space in final file should be in CMYK.

The details that need to be included on the card:

- Use the provided Logo
- Name: Wiktor Baranowski
- Email:   sales@vistalumeworks.com.au
- Website:    vistalumeworks.com.au
- Twitter:    chirpline.com/vistalumeworks
- Facebook:   folkcircle.com/vistalumeworks
- Mobile  0417 539 662

Please use the attached template to design the logo to the specified size, including the marked bleed lines. I have also attached my logo in PNG (transparent background) and ai format for you to use.

The final file should be:
- Photoshop version with layers so I can edit the name/text etc. All non vector files should be high resolution at 1039 x 697 pixels at 300 dpi.

I also require a file as:
- Vector based PDF

Anyway questions please contact me.

Thank you

Industry/Entity Type

Landscape

Logo styles of interest
Pictorial/Combination Logo
Abstract Logo
Wordmark Logo
Lettermark Logo
Requirements
Must have
• The details that need to be included on the card:

- Use the provided Logo
- Name: Wiktor Baranowski
- Email: sales@vistalumeworks.com.au
- Website: vistalumeworks.com.au
- Twitter: chirpline.com/vistalumeworks
- Facebook: folkcircle.com/vistalumeworks
- Mobile 0417 539 662

```html
<!DOCTYPE html>
<html lang="en">
<head>
<meta charset="utf-8">
<title>Vistalume Works – Business Cards</title>
<link rel="stylesheet" href="https://fonts.googleapis.com/css2?family=Cinzel:wght@400&family=Mulish:wght@400;600&display=swap">
<style>
  :root {
    --backdrop: #2d2d30;
    --card: #3d3e50;
    --ink: #ffffff;
    --ink-soft: #e6e6ec;
    --mark: #ffffff;
  }
  * { box-sizing: border-box; margin: 0; padding: 0; }
  html, body {
    width: 1200px; height: 900px; overflow: hidden;
    background: var(--backdrop);
  }
  .canvas { position: relative; width: 1200px; height: 900px; }
  .card {
    position: absolute;
    background: var(--card);
    border-radius: 18px;
    color: var(--ink);
  }
  .card--front { left: 186px; top: 308px; width: 515px; height: 284px; }
  .card--back  { left: 730px; top: 193px; width: 285px; height: 513px; }

  .brand { position: absolute; left: 0; right: 0; text-align: center; }
  .brand__dot {
    display: block; margin: 0 auto;
    border-radius: 50%; background: var(--mark);
  }
  .brand__name {
    display: block;
    font-family: "Cinzel", serif;
    font-weight: 400;
    color: var(--ink);
    letter-spacing: 0.02em;
    white-space: nowrap;
  }
  .card--front .brand { top: 66px; }
  .card--front .brand__dot { width: 93px; height: 93px; }
  .card--front .brand__name { font-size: 27px; margin-top: 16px; }

  .card--back .brand { top: 42px; }
  .card--back .brand__dot { width: 74px; height: 74px; }
  .card--back .brand__name { font-size: 20px; margin-top: 10px; }

  .contact {
    position: absolute; left: 44px; top: 364px;
    font-family: "Mulish", sans-serif;
  }
  .contact__name { font-size: 18px; font-weight: 400; color: var(--ink); margin-bottom: 10px; }
  .contact__list { list-style: none; }
  .contact__item {
    display: flex; align-items: center;
    font-size: 12px; line-height: 16.4px; color: var(--ink-soft);
    white-space: nowrap;
  }
  .contact__label {
    width: 22px; font-weight: 600; font-size: 11px; color: var(--ink);
  }
  .contact__square {
    display: inline-block; width: 10px; height: 10px;
    background: var(--ink); border-radius: 1px; margin-right: 12px;
  }
</style>
</head>
<body>
<main class="canvas">
  <section class="card card--front" aria-label="Card front">
    <div class="brand">
      <span class="brand__dot"></span>
      <span class="brand__name">Vistalume Works</span>
    </div>
  </section>

  <section class="card card--back" aria-label="Card back">
    <div class="brand">
      <span class="brand__dot"></span>
      <span class="brand__name">Vistalume Works</span>
    </div>
    <div class="contact">
      <p class="contact__name">Wiktor Baranowski</p>
      <ul class="contact__list">
        <li class="contact__item"><span class="contact__label">M</span>0417 539 662</li>
        <li class="contact__item"><span class="contact__label">E</span>sales@vistalumeworks.com.au</li>
        <li class="contact__item"><span class="contact__label">W</span>vistalumeworks.com.au</li>
        <li class="contact__item"><span class="contact__square"></span>folkcircle.com/vistalumeworks</li>
        <li class="contact__item"><span class="contact__square"></span>chirpline.com/vistalumeworks</li>
      </ul>
    </div>
  </section>
</main>
</body>
</html>
```